Flyer to promote an IT Innovation Fest

BWL Spark Summit 2018

We are looking to implement a new Innovation program that uses the Morvane LaunchCrate concept. Team Members will receive a red box that contains a set of 20 flash cards that help them to bring an innovative idea to life (based on a business problem or friction point).
We are looking to create a cover page for our 'Red Box' via way of a 1 page flyer.
We want to call it the 'BWL Spark Summit 2018'. We would like the 1 page flyer to look super cool and also have some kind of cool cartoon imagery to bring it to life.
We also want to incorporate our logo into the page somewhere as well.

Ideally, we'd also like to get a logo called 'Spark Summit' that we could use on some of our collateral as well. I thought it might be best to create the 1 pager flyer first, then we could look to pull a Spark Summit logo off that. Please let me know though whether it would be easier to create the logo first, then create the flyer).

Bluewater Labs are a support business to Bluewater Journeys Group which is the largest travel retailer in Australia. Our IT area has around 150 permanent team members. We have a fun culture and can push the boundaries with our imagery as the flyer will be for internal distribution only.

I have attached the Morvane Flash cards that this 1 pager will be the cover page for.

Target Market(s)

Members of the Bluewater Labs team (internal marketing)

Industry/Entity Type

It Company

Requirements
Must have
• Our BWL Logo
• A super cool, innovative, funky look (with some kind of cartoon imagery)
• We need to be able to edit the flyer to add some text
Nice to have
• Stay within the colour theme of the 'Start Here' page on the Morvane attachment

```html
<!DOCTYPE html>
<html lang="en">
<head>
<meta charset="utf-8">
<title>BWL Spark Summit 2018 — Flyer</title>
<link rel="stylesheet" href="https://fonts.googleapis.com/css2?family=Montserrat:wght@100;400;700;800;900&family=Oswald:wght@600&display=swap">
<style>
  :root {
    --page-bg: #e4e4e4;
    --red-deep: #6c0d22;
    --red-mid: #8c1429;
    --red-bright: #a81c2e;
    --white: #ffffff;
    --ink: #1c1c1c;
    --digit: #2e2e2e;
    --accent-red: #d5232f;
    --base-strip: #111111;
    --illustration-light: #f4f1f1;
    --illustration-shade: #c9c2c2;
  }
  * { margin: 0; padding: 0; box-sizing: border-box; }
  html, body {
    width: 1200px;
    height: 1200px;
    overflow: hidden;
    background: var(--page-bg);
  }
  .canvas {
    position: relative;
    width: 1200px;
    height: 1200px;
  }
  .flyer {
    position: absolute;
    left: 200px;
    top: 35px;
    width: 800px;
    height: 1130px;
    box-shadow: 0 10px 30px rgba(0,0,0,0.18);
  }
  .flyer svg { display: block; width: 100%; height: 100%; }
  .title-brand { font-family: "Montserrat", sans-serif; font-weight: 900; fill: var(--white); }
  .title-word { font-family: "Oswald", sans-serif; font-weight: 600; fill: var(--white); }
  .title-thin { font-family: "Montserrat", sans-serif; font-weight: 100; fill: var(--white); }
  .year { font-family: "Montserrat", sans-serif; font-weight: 900; fill: var(--digit); }
  .brand-name { font-family: "Montserrat", sans-serif; font-weight: 700; fill: var(--accent-red); }
  .cta-label { font-family: "Montserrat", sans-serif; font-weight: 400; fill: var(--accent-red); }
  .cta-phone { font-family: "Montserrat", sans-serif; font-weight: 800; fill: var(--ink); }
</style>
</head>
<body>
<main class="canvas">
  <article class="flyer">
    <svg viewBox="0 0 800 1130" xmlns="http://www.w3.org/2000/svg">
      <defs>
        <linearGradient id="hero-red" x1="0" y1="0" x2="1" y2="1">
          <stop offset="0" stop-color="var(--red-deep)"/>
          <stop offset="0.45" stop-color="var(--red-bright)"/>
          <stop offset="0.75" stop-color="var(--red-mid)"/>
          <stop offset="1" stop-color="var(--red-deep)"/>
        </linearGradient>
        <linearGradient id="illustration-fill" x1="0" y1="0" x2="0" y2="1">
          <stop offset="0" stop-color="var(--illustration-light)"/>
          <stop offset="0.75" stop-color="var(--illustration-light)"/>
          <stop offset="1" stop-color="var(--illustration-shade)" stop-opacity="0.35"/>
        </linearGradient>
      </defs>

      <!-- hero panel -->
      <rect class="hero" x="0" y="0" width="800" height="924" fill="url(#hero-red)"/>
      <rect class="hero-frame" x="18" y="14" width="766" height="909" fill="none" stroke="var(--white)" stroke-opacity="0.6" stroke-width="1"/>

      <!-- cartoon illustration area -->
      <g class="hero-illustration" role="img" aria-label="Cartoon of a cheerful office worker in a tie riding a light bulb that rises with speed lines beneath it">
        <rect x="68" y="134" width="194" height="696" rx="96" fill="url(#illustration-fill)" opacity="0.9"/>
      </g>

      <!-- event title -->
      <text class="title-brand" x="318" y="318" font-size="214" textLength="425" lengthAdjust="spacingAndGlyphs">BWL</text>
      <text class="title-word" x="316" y="446" font-size="138" textLength="424" lengthAdjust="spacingAndGlyphs">SPARK</text>
      <text class="title-thin" x="322" y="605" font-size="176" textLength="420" lengthAdjust="spacingAndGlyphs">SUMMIT</text>

      <rect class="year-box" x="321" y="620" width="420" height="157" fill="var(--white)"/>
      <text class="year" x="531" y="756" font-size="156" text-anchor="middle" letter-spacing="-6">2018</text>

      <!-- footer -->
      <rect class="footer" x="0" y="924" width="800" height="176" fill="var(--white)"/>
      <rect class="footer-strip" x="0" y="1100" width="800" height="30" fill="var(--base-strip)"/>

      <g class="footer-brand">
        <circle cx="155" cy="983" r="30" fill="none" stroke="var(--accent-red)" stroke-width="4"/>
        <text class="brand-name" x="155" y="1047" font-size="23" text-anchor="middle">Bluewater Labs</text>
      </g>

      <g class="footer-contact">
        <text class="cta-label" x="739" y="1005" font-size="29" text-anchor="end">Call Us Now</text>
        <text class="cta-phone" x="739" y="1056" font-size="50" text-anchor="end" letter-spacing="-1">61 7 3555 0142</text>
      </g>
    </svg>
  </article>
</main>
</body>
</html>
```